Business Card Design Project - del varosi group

dear Sirs

we need business card design for our group ( DEL Varosi Group ) , i have got the Logo design of our group from pixel harbor in previous , so all need details relating to our group i think available with you, as well as the the chosen logo design

we hope to provide us with business card logo that to be appropaite and satisfactory to us .

thanks

note : logo design of our group is attached .
Updates

Reason: please extend the deadline of my project for additional 15 days because i didn't received appropriate design for our gruop yet . kindly beaware that i have received 77 design till now , supossed to send me 200-250 design at least . thanks

Target Market(s)

contents

name : Kerem EL Nadiri

position : Operation Manager

Industry/Entity Type

Business

Requirements
Must have

• person name

group logo
Nice to have
• logo color matching with back background

```html
<!DOCTYPE html>
<html lang="en">
<head>
<meta charset="utf-8">
<title>DEL Varosi Group — Business Card</title>
<link rel="stylesheet" href="https://fonts.googleapis.com/css2?family=Lato:wght@400;700&display=swap">
<style>
  :root {
    --canvas-bg: #e9e7e3;
    --card-white: #f7f8fa;
    --brand-blue: #1f4fa0;
    --ink: #2b2b2b;
    --rule-blue: #2f6cb5;
    --gold-light: #e4c64a;
    --gold-mid: #c9a21a;
    --gold-deep: #b48a12;
  }
  * { box-sizing: border-box; margin: 0; padding: 0; }
  html, body {
    width: 1200px; height: 720px; overflow: hidden;
    background: var(--canvas-bg);
    font-family: "Lato", sans-serif;
  }
  .canvas {
    position: relative; width: 1200px; height: 720px;
    display: flex; align-items: center; justify-content: center; gap: 50px;
  }
  .card {
    width: 525px; height: 300px; border-radius: 3px;
    box-shadow: 0 6px 18px rgba(0,0,0,.12);
    position: relative; overflow: hidden;
  }
  .card--front { background: var(--card-white); color: var(--ink); }
  .card--back {
    background: radial-gradient(ellipse at 45% 35%, var(--gold-light) 0%, var(--gold-mid) 55%, var(--gold-deep) 100%);
    display: flex; align-items: center; justify-content: center;
  }
  .brand {
    display: flex; align-items: center; gap: 10px;
    color: var(--brand-blue); font-weight: 700;
    text-transform: uppercase; letter-spacing: 1px;
  }
  .brand__mark {
    width: 14px; height: 14px; background: var(--brand-blue);
  }
  .card--front .brand { justify-content: center; margin-top: 34px; font-size: 30px; }
  .card--back .brand { font-size: 44px; }
  .card--back .brand__mark { width: 20px; height: 20px; }
  .person { text-align: center; margin-top: 22px; }
  .person__name { font-size: 22px; font-weight: 400; }
  .person__role { font-size: 13px; margin-top: 2px; }
  .rule {
    height: 1px; margin: 12px 30px;
    background: linear-gradient(90deg, transparent, var(--rule-blue), transparent);
  }
  .contact { font-size: 12px; padding: 0 30px; line-height: 1.7; }
  .contact__row { display: flex; justify-content: space-between; }
  .contact__row--center { justify-content: center; }
  .contact__web { font-weight: 700; }
</style>
</head>
<body>
<main class="canvas">
  <section class="card card--front">
    <div class="brand"><span class="brand__mark"></span>DEL Varosi Group</div>
    <div class="person">
      <h1 class="person__name">Kerem EL Nadiri</h1>
      <p class="person__role">Operation Manager</p>
    </div>
    <div class="rule"></div>
    <div class="contact">
      <div class="contact__row">
        <span>t: (240) 41 506 22 18</span>
        <span>f: (240) 41 506 22 19</span>
        <span>m: (240) 78 214 63 05</span>
      </div>
      <div class="contact__row">
        <span>e: kerem-nadiri@del-varosi.com</span>
        <span class="contact__web">www.del-varosi.com</span>
      </div>
      <div class="contact__row contact__row--center">
        <span>Rue des Palmiers - Port Sud BP 218 - Lomara, Veldia</span>
      </div>
    </div>
    <div class="rule"></div>
  </section>
  <section class="card card--back">
    <div class="brand"><span class="brand__mark"></span>DEL Varosi Group</div>
  </section>
</main>
</body>
</html>
```